Lantern Petals Website v.1 - attract floral shop franchisees

I need a simple information website for my new business. We are a franchisor of flower shops. The overall purpose of the website is to promote the company and the service, especially to potential franchisees and retailers. Only about 4 pages are required including homepage, About, For Supermarkets, For Franchisees, and Contact. No special functions are required except the site will have two separate inquiry forms that must be filled out online and submitted via automated email. Similarly, an email form should be linked from the Contact page. I have a logo and business cards designed by ArtMingle, and I would like the site to have a consistent color scheme and style. The key to design will be to express the joy and love associated with flowers and floral bouquets.
IMPORTANT - I will be exporting the website design to Wordpress CMS in a site hosted by HostNimbus. For smooth integration into WordPress hosted by HostNimbus, the designer should build the site using a WordPress-friendly format. Ideally, they should use HTML, CSS, and PHP. Creating a custom theme or using a page builder that exports to WordPress-compatible files is best. This ensures the site can be easily imported and managed within WordPress.

Target Market(s)

Potential franchisees (existing florists or creative types who might like to own a floral business) and supermarkets who might want us to run their floral department

Industry/Entity Type

Floral retailing

Requirements
Must have
• A brand theme that is beautiful, consistent throughout and builds on the logo design
Nice to have
• Show gender and ethnic diversity in customers and florists. Pictures of happy florists (for franchisees) and pictures of amazing floral department displays (for supermarkets)

```html
<!DOCTYPE html>
<html lang="en">
<head>
<meta charset="utf-8">
<title>Lantern Petals – Franchisor of Flower Shops</title>
<link rel="stylesheet" href="https://fonts.googleapis.com/css2?family=Hind:wght@600;700&family=Jost:wght@400;500&family=Montserrat:wght@400;500&display=swap">
<style>
:root{
  --green:#0b8f46;
  --green-dark:#067a3a;
  --orange:#f0ae2e;
  --ink:#111111;
  --white:#ffffff;
  --rule:#e9c88a;
}
*{margin:0;padding:0;box-sizing:border-box}
html,body{width:1200px;height:3043px;overflow:hidden;background:var(--white);color:var(--ink)}
body{position:relative;font-family:'Montserrat',sans-serif}
a{color:inherit;text-decoration:none}

.icon-ring{width:48px;height:48px;border:2px solid var(--orange);border-radius:50%;display:flex;align-items:center;justify-content:center;flex:none}
.icon-ring svg{width:22px;height:22px;fill:var(--green)}
.contact-item{display:flex;align-items:center;gap:16px;font-size:22px;font-weight:400}

/* header */
.site-header{position:absolute;top:0;left:0;width:1200px;height:197px}
.site-header .phone{position:absolute;left:130px;top:35px}
.site-header .email{position:absolute;left:737px;top:35px}
.brand{position:absolute;left:480px;top:30px;width:240px;display:flex;align-items:center;gap:12px;justify-content:center}
.brand-dot{width:46px;height:46px;border-radius:50%;background:var(--orange);flex:none}
.brand-name{font-family:'Jost',sans-serif;font-weight:500;font-size:30px;color:var(--green);white-space:nowrap}
.main-nav{position:absolute;left:98px;top:117px;width:1004px;border-top:1.5px solid var(--rule);display:flex;justify-content:center;padding-top:21px;font-size:21px}
.main-nav a{padding:0 31px;border-left:1.5px solid var(--green);line-height:22px}
.main-nav a:first-child{border-left:none}

/* hero */
.hero{position:absolute;top:197px;left:0;width:1200px;height:795px;overflow:hidden}
.hero-photo{position:absolute;inset:0;background:
  radial-gradient(circle at 8% 45%,rgba(226,140,160,.75) 0,rgba(226,140,160,0) 170px),
  radial-gradient(circle at 20% 40%,rgba(240,236,226,.55) 0,rgba(240,236,226,0) 120px),
  radial-gradient(circle at 92% 40%,rgba(236,196,120,.6) 0,rgba(236,196,120,0) 190px),
  radial-gradient(circle at 78% 28%,rgba(110,120,170,.55) 0,rgba(110,120,170,0) 130px),
  radial-gradient(circle at 85% 85%,rgba(235,210,60,.75) 0,rgba(235,210,60,0) 230px),
  radial-gradient(circle at 55% 8%,rgba(70,120,60,.8) 0,rgba(70,120,60,0) 260px),
  radial-gradient(ellipse at 50% 60%,#7a5234 0%,#5a3a24 40%,#3a4a2a 75%,#2f5a2e 100%)}
.hero-card{position:absolute;left:332px;top:125px;width:536px;height:283px;border-radius:22px;background:rgba(11,143,70,.84);text-align:center;color:var(--white)}
.hero-card h1{font-family:'Hind',sans-serif;font-weight:700;font-size:62px;letter-spacing:1px;margin-top:50px;line-height:1}
.hero-card p{font-family:'Jost',sans-serif;font-size:23px;margin-top:24px;letter-spacing:.3px}
.btn{display:inline-flex;align-items:center;justify-content:center;border-radius:30px;font-family:'Hind',sans-serif;font-weight:700;color:var(--white);letter-spacing:.5px}
.btn-orange{background:var(--orange)}
.btn-green{background:var(--green)}
.hero-card .btn{width:182px;height:57px;font-size:23px;margin-top:20px}
.hero-wave{position:absolute;left:0;top:483px;width:1200px;height:320px}

/* audience cards */
.audience{position:absolute;top:1071px;left:98px;width:1004px;display:flex;gap:29px}
.audience-card{width:487px;text-align:center}
.audience-photo{height:308px;border-radius:26px}
.audience-photo.supermarket{background:
  radial-gradient(circle at 70% 60%,rgba(230,90,60,.8) 0,rgba(230,90,60,0) 110px),
  radial-gradient(circle at 88% 75%,rgba(240,200,50,.8) 0,rgba(240,200,50,0) 90px),
  radial-gradient(circle at 62% 30%,rgba(230,170,190,.8) 0,rgba(230,170,190,0) 90px),
  radial-gradient(circle at 25% 50%,rgba(200,180,150,.9) 0,rgba(200,180,150,0) 120px),
  linear-gradient(135deg,#6f6352 0%,#a89a80 40%,#5f8a3c 75%,#3f6a2c 100%)}
.audience-photo.franchise{background:
  radial-gradient(circle at 55% 55%,rgba(200,170,130,.8) 0,rgba(200,170,130,0) 70px),
  radial-gradient(circle at 30% 25%,rgba(230,120,140,.7) 0,rgba(230,120,140,0) 90px),
  radial-gradient(circle at 20% 75%,rgba(120,170,80,.8) 0,rgba(120,170,80,0) 110px),
  radial-gradient(circle at 85% 50%,rgba(110,150,80,.8) 0,rgba(110,150,80,0) 110px),
  linear-gradient(90deg,#4a5a3a 0%,#2c3129 50%,#4f6a3c 100%)}
.audience-card h2{font-family:'Hind',sans-serif;font-weight:700;font-size:40px;letter-spacing:1.5px;margin-top:24px}

/* about */
.about{position:absolute;top:1525px;left:0;width:1200px;height:558px;background:
  radial-gradient(ellipse at 72% 70%,rgba(140,150,50,.85) 0,rgba(140,150,50,0) 170px),
  radial-gradient(circle at 78% 35%,rgba(214,160,120,.8) 0,rgba(214,160,120,0) 110px),
  radial-gradient(circle at 65% 75%,rgba(235,170,180,.7) 0,rgba(235,170,180,0) 120px),
  linear-gradient(90deg,var(--green) 0%,var(--green) 40%,#3aa861 52%,#a9c49a 66%,#e8dfcf 85%,#d9d2c7 100%)}
.about-inner{position:absolute;left:105px;top:62px;width:470px;color:var(--white)}
.about h2{font-family:'Hind',sans-serif;font-weight:700;font-size:42px;letter-spacing:1px;line-height:1}
.about p{font-family:'Jost',sans-serif;font-size:15.5px;line-height:30px;margin-top:24px}
.about p + p{margin-top:20px}
.about .btn{width:182px;height:56px;font-size:20px;margin-top:44px}

/* contact */
.contact{position:absolute;top:2180px;left:0;width:1200px;text-align:center}
.contact h2{font-family:'Hind',sans-serif;font-weight:700;font-size:44px;letter-spacing:1px;line-height:1}
.contact .lead{font-family:'Jost',sans-serif;font-size:15px;margin-top:22px}
.contact-row{display:flex;justify-content:center;gap:76px;margin-top:26px}
.inquiry-row{display:flex;justify-content:center;gap:22px;margin-top:42px}
.inquiry-row .btn{height:56px;font-size:19px;padding:0 34px}

/* footer */
.site-footer{position:absolute;top:2440px;left:0;width:1200px;height:603px;color:var(--white)}
.footer-wave{position:absolute;left:0;top:0;width:1200px;height:603px}
.footer-brand{position:absolute;left:100px;top:190px;display:flex;align-items:center;gap:24px}
.footer-brand .brand-dot{width:150px;height:150px}
.footer-brand .brand-name{font-size:76px;color:var(--orange)}
.footer-nav{position:absolute;left:130px;top:418px;display:flex;gap:62px;font-size:21px}
.copyright{position:absolute;left:132px;top:508px;font-family:'Hind',sans-serif;font-weight:600;font-size:17px;letter-spacing:.3px}
.social{position:absolute;left:842px;top:497px;display:flex;gap:6px}
.social span{width:41px;height:41px;border:2px solid var(--white);border-radius:50%}
</style>
</head>
<body>

<header class="site-header">
  <div class="contact-item phone">
    <span class="icon-ring"><svg viewBox="0 0 24 24"><path d="M6.6 10.8a15.1 15.1 0 0 0 6.6 6.6l2.2-2.2c.3-.3.7-.4 1-.2 1.1.4 2.3.6 3.6.6.6 0 1 .4 1 1V20c0 .6-.4 1-1 1A17 17 0 0 1 3 4c0-.6.4-1 1-1h3.5c.6 0 1 .4 1 1 0 1.3.2 2.5.6 3.6.1.3 0 .7-.2 1z"/></svg></span>
    <span>+ 1.555.204.7718</span>
  </div>
  <a class="brand" href="#"><span class="brand-dot"></span><span class="brand-name">Lantern Petals</span></a>
  <div class="contact-item email">
    <span class="icon-ring"><svg viewBox="0 0 24 24"><path d="M2 5h20v3l-10 6L2 8zm0 5.3 10 6 10-6V19H2z"/></svg></span>
    <span>mara@lanternpetals-shops.com</span>
  </div>
  <nav class="main-nav">
    <a href="#">ABOUT</a><a href="#">FOR SUPERMARKETS</a><a href="#">FOR FRANCHISEES</a><a href="#">CONTACT</a>
  </nav>
</header>

<section class="hero">
  <div class="hero-photo" role="img" aria-label="Overhead view of a florist's wooden workbench with hands wrapping a bouquet among fresh flowers, twine and ribbon"></div>
  <div class="hero-card">
    <h1>LANTERN PETALS</h1>
    <p>FRANCHISOR OF FLOWER SHOPS</p>
    <a class="btn btn-orange" href="#">BUY NOW</a>
  </div>
  <svg class="hero-wave" viewBox="0 0 1200 320" preserveAspectRatio="none" aria-hidden="true">
    <path fill="#f0ae2e" d="M0,0 C250,-20 500,110 720,230 C900,320 1100,310 1200,295 L1200,320 L0,320 Z"/>
    <path fill="#ffffff" d="M0,132 C300,70 600,200 820,278 C1000,330 1150,318 1200,310 L1200,320 L0,320 Z"/>
    <path fill="#0b8f46" d="M0,170 C180,122 380,138 502,218 C350,188 150,208 0,246 Z"/>
  </svg>
</section>

<section class="audience">
  <div class="audience-card">
    <div class="audience-photo supermarket" role="img" aria-label="Florist arranging colourful bouquets at a supermarket floral department"></div>
    <h2>SUPERMARKETS</h2>
  </div>
  <div class="audience-card">
    <div class="audience-photo franchise" role="img" aria-label="Smiling florist holding tulips in the doorway of her flower shop surrounded by potted plants"></div>
    <h2>FRANCHISEES</h2>
  </div>
</section>

<section class="about" role="img" aria-label="Florist smiling while arranging a bouquet in a bright shop, fading into green">
  <div class="about-inner">
    <h2>ABOUT</h2>
    <p>Fresh flowers convey beauty and love, and in our view should become something every person regularly enjoys.&nbsp; Lantern Petals is an entrepreneurial company created to make top quality fresh flowers and professionally-designed bouquets accessible to every consumer at affordable prices.</p>
    <p>Professional florists typically sell the finest quality stems, design the most beautiful bouquets and provide the finest customer service, but their costs – of floral products</p>
    <a class="btn btn-orange" href="#">READ MORE</a>
  </div>
</section>

<section class="contact">
  <h2>CONTACT US</h2>
  <p class="lead">Lorem ipsum dolor sit amet, consectetur adipiscing elit, sed do eiusmod tempor incididunt</p>
  <div class="contact-row">
    <div class="contact-item">
      <span class="icon-ring"><svg viewBox="0 0 24 24"><path d="M6.6 10.8a15.1 15.1 0 0 0 6.6 6.6l2.2-2.2c.3-.3.7-.4 1-.2 1.1.4 2.3.6 3.6.6.6 0 1 .4 1 1V20c0 .6-.4 1-1 1A17 17 0 0 1 3 4c0-.6.4-1 1-1h3.5c.6 0 1 .4 1 1 0 1.3.2 2.5.6 3.6.1.3 0 .7-.2 1z"/></svg></span>
      <span>+ 1.555.204.7718</span>
    </div>
    <div class="contact-item">
      <span class="icon-ring"><svg viewBox="0 0 24 24"><path d="M2 5h20v3l-10 6L2 8zm0 5.3 10 6 10-6V19H2z"/></svg></span>
      <span>mara@lanternpetals-shops.com</span>
    </div>
  </div>
  <div class="inquiry-row">
    <a class="btn btn-orange" href="#">NEW FLORIST FRANCHISE INQUIRY</a>
    <a class="btn btn-green" href="#">PROFESSIONAL FLORIST FRANCHISE INQUIRY</a>
  </div>
</section>

<footer class="site-footer">
  <svg class="footer-wave" viewBox="0 0 1200 603" preserveAspectRatio="none" aria-hidden="true">
    <path fill="#111111" d="M0,46 C250,40 500,150 700,235 C850,290 1000,332 1200,330 L1200,603 L0,603 Z"/>
    <path fill="#f0ae2e" d="M0,34 C250,20 500,60 697,118 C850,165 1050,196 1200,196 L1200,330 C1000,332 850,290 700,235 C500,150 250,40 0,46 Z"/>
    <path fill="#0b8f46" d="M690,112 C850,104 1050,106 1200,111 L1200,188 C1050,188 850,160 690,112 Z"/>
  </svg>
  <div class="footer-brand"><span class="brand-dot"></span><span class="brand-name">Lantern Petals</span></div>
  <nav class="footer-nav">
    <a href="#">ABOUT</a><a href="#">FOR SUPERMARKETS</a><a href="#">FOR FRANCHISEES</a><a href="#">CONTACT</a>
  </nav>
  <p class="copyright">COPYRIGHT © 2024 LANTERN PETALS &nbsp;|&nbsp; ALL RIGHTS RESERVED.</p>
  <div class="social" aria-label="Social media links">
    <span></span><span></span><span></span><span></span><span></span>
  </div>
</footer>

</body>
</html>
```